Business card for a Exhibition booth fabrication company

Hi. My company would like to change our corporate name card. We are an events and Exhibition stand builder company. We would like our corporate name card to resonate what we do. I need someone to create something unique that relates to the industry that I am in. The graphic designer should be creative to incorporate the elements of my industry and try to blend in well in the design of the card. Our aim is to ensure that we are unique and our card can look different from our competitors.
Updates

Target Market(s)

Marketing and events manager from all companies

Contact Information for Business Card

The business card should have the following details:
Name
Job Title
Email
Website

Colors

Designer to choose colors to be used in the design.

Requirements
Must have
• The card must be look something that is relevant to the service that I am providing. My website is: www.velmora-buildworks.com
• You can see my website to get more information on what service that I am doing
Nice to have
• On the back of my card, I would like to have a globe image with the incorporation of my company logo. This is to indicate that my services can be done in any part of the world.

```html
<!DOCTYPE html>
<html lang="en">
<head>
<meta charset="utf-8">
<title>Velmora Buildworks – Business Card</title>
<link href="https://fonts.googleapis.com/css2?family=Open+Sans:wght@400;600&family=Roboto:wght@400;700&display=swap" rel="stylesheet">
<style>
  :root {
    --stage-light: #dcdddf;
    --stage-dark: #a4a5a8;
    --card-white: #ffffff;
    --brand-red: #ed1c24;
    --brand-grey: #636466;
    --text-grey: #5a5b5d;
    --rule-grey: #c8c8c8;
    --map-tone: #7d7e80;
    --back-text: #f2f2f2;
  }
  * { margin: 0; padding: 0; box-sizing: border-box; }
  html, body { width: 1200px; height: 1118px; overflow: hidden; }
  body {
    position: relative;
    background: linear-gradient(90deg, var(--stage-light) 0%, var(--stage-dark) 100%);
    font-family: "Open Sans", Arial, sans-serif;
  }
  .card {
    position: absolute;
    width: 755px;
    height: 430px;
    border-radius: 36px;
    overflow: hidden;
  }
  .card-front { left: 221px; top: 96px; background: var(--card-white); }
  .card-back { left: 223px; top: 584px; background: var(--brand-grey); }

  .front-waves { position: absolute; left: 0; top: 0; width: 755px; height: 430px; }

  .brand-block {
    position: absolute;
    left: 40px;
    top: 238px;
    width: 350px;
    display: flex;
    align-items: center;
    justify-content: center;
    gap: 10px;
    white-space: nowrap;
  }
  .brand-square { width: 13px; height: 13px; background: var(--brand-red); flex: none; }
  .brand-name {
    font-family: "Open Sans", Arial, sans-serif;
    font-weight: 600;
    font-size: 20px;
    letter-spacing: 1px;
    color: var(--brand-grey);
    text-transform: uppercase;
  }

  .divider {
    position: absolute;
    left: 405px;
    top: 97px;
    width: 2px;
    height: 226px;
    background: var(--rule-grey);
  }
  .details { position: absolute; left: 424px; top: 88px; color: var(--text-grey); }
  .person-name {
    font-family: "Roboto", Arial, sans-serif;
    font-weight: 700;
    font-size: 27px;
    color: var(--brand-red);
    letter-spacing: 0.5px;
  }
  .person-title {
    font-family: "Roboto", Arial, sans-serif;
    font-size: 20px;
    letter-spacing: 1px;
    margin-top: 2px;
  }
  .address { font-size: 18px; line-height: 26px; margin-top: 16px; }
  .contact-list { list-style: none; margin-top: 14px; }
  .contact-list li {
    display: flex;
    align-items: center;
    font-size: 18px;
    height: 35px;
    white-space: nowrap;
  }
  .contact-icon {
    display: block;
    width: 18px;
    height: 18px;
    flex: 0 0 18px;
    margin-right: 14px;
  }

  .map-area {
    position: absolute;
    left: 0;
    top: 75px;
    width: 755px;
    height: 265px;
    background: radial-gradient(ellipse at center, var(--map-tone) 0%, rgba(125,126,128,0.55) 60%, rgba(125,126,128,0) 100%);
  }
  .back-brand {
    position: absolute;
    left: 0;
    top: 180px;
    width: 755px;
    text-align: center;
    font-family: "Open Sans", Arial, sans-serif;
    font-weight: 600;
    font-size: 40px;
    letter-spacing: 3px;
    color: #c9cacb;
    text-transform: uppercase;
  }
  .back-web {
    position: absolute;
    left: 0;
    bottom: 14px;
    width: 755px;
    text-align: center;
    font-size: 21px;
    letter-spacing: 4px;
    color: var(--back-text);
  }
</style>
</head>
<body>

  <section class="card card-front" aria-label="Card front">
    <svg class="front-waves" viewBox="0 0 667 380" preserveAspectRatio="none" aria-hidden="true">
      <path fill="var(--brand-grey)" d="M0 325 C120 315 260 338 400 350 C520 360 610 330 667 306 L667 334 C560 360 440 372 330 366 C200 360 80 345 0 352 Z"/>
      <path fill="var(--card-white)" d="M220 325 L460 370 L440 370 Z"/>
      <path fill="var(--brand-red)" d="M0 362 C100 350 230 356 360 366 C500 376 600 356 667 340 V380 H0 Z"/>
    </svg>

    <div class="brand-block">
      <span class="brand-square"></span>
      <span class="brand-name">Velmora Buildworks</span>
    </div>

    <div class="divider"></div>

    <div class="details">
      <p class="person-name">DANIEL HARCOURT</p>
      <p class="person-title">PRESIDENT</p>
      <p class="address">Street Name, City Name<br>Zipcode - 01234</p>
      <ul class="contact-list">
        <li>
          <svg class="contact-icon" width="18" height="18" viewBox="0 0 24 24" aria-hidden="true"><path fill="var(--brand-red)" d="M6.6 10.8c1.4 2.8 3.8 5.1 6.6 6.6l2.2-2.2c.3-.3.7-.4 1-.2 1.1.4 2.3.6 3.6.6.6 0 1 .4 1 1V20c0 .6-.4 1-1 1C10.6 21 3 13.4 3 4c0-.6.4-1 1-1h3.5c.6 0 1 .4 1 1 0 1.3.2 2.5.6 3.6.1.3 0 .7-.2 1z"/></svg>
          <span>012-555-0148</span>
        </li>
        <li>
          <svg class="contact-icon" width="18" height="18" viewBox="0 0 24 24" aria-hidden="true"><rect x="2" y="5" width="20" height="14" fill="var(--brand-red)"/><path d="M2 5 L12 13 L22 5" fill="none" stroke="#fff" stroke-width="1.6"/></svg>
          <span>info@velmora-buildworks.com</span>
        </li>
        <li>
          <svg class="contact-icon" width="18" height="18" viewBox="0 0 24 24" aria-hidden="true"><g fill="none" stroke="var(--brand-red)" stroke-width="1.8"><circle cx="12" cy="12" r="9.5"/><ellipse cx="12" cy="12" rx="4" ry="9.5"/><path d="M2.5 12h19M4 7h16M4 17h16"/></g></svg>
          <span>www.velmora-buildworks.com</span>
        </li>
      </ul>
    </div>
  </section>

  <section class="card card-back" aria-label="Card back">
    <div class="map-area" role="img" aria-label="World map in light grey spanning the card"></div>
    <p class="back-brand">Velmora Buildworks</p>
    <p class="back-web">www.velmora-buildworks.com</p>
  </section>

</body>
</html>
```